Business Card Design Project : Ridgeline Press

In preparation for market launch, Tamarind's Ridgeline Press require the development of a business card. Ridgeline Press is a Community online publishing web portal. We provide the the city of Whistler located in B.C. (Canada) business directories, News, Classified ads, News, Events and blogs etc.

The main focus of the brand is to help local businesses to corporate with their online advertisement and marketing. Meeting our clients face to face is a must (B2B).

Target Market(s)

The target market is B2B customers. Business Owners to Marketing, advertising Managers

Industry/Entity Type

Business

Requirements
Must have
• - The business card will be two sided.
the BACK side will have our logo which consist of (icon, url,slogan) submited. The logo will be middle and centred.

The FRONT side should have company details:

Company Legal Name: TAMARIND RIDGELINE MEDIA

Owen Farsk
Director of Sales & Marketing

www.tamarindridgeline.biz
owen@tamarindridgeline.biz

Phone: 604 317 8842
#2714 - 582 E. Halvern St.
Vancouver, B.C. V7K2R4 Canada
Nice to have
• - For the "FRONT" side of our business card. You can separate or re-arrange with our logo components (icon, logo,slogan). It does not have to be together.

Also our company legal name is rather long so arrange or organize the name in a way to make it shorter. Your experience and creativity will have to come in play.
Should not have
• should not have other colors beside logo color and black text (2 colors). Also nothing Three dimensional

```html
<!DOCTYPE html>
<html lang="en">
<head>
<meta charset="utf-8">
<title>Ridgeline Press – Business Card</title>
<link href="https://fonts.googleapis.com/css2?family=Open+Sans:wght@400;600;800&display=swap" rel="stylesheet">
<style>
  :root {
    --brand-blue: #1a7fd0;
    --ink: #1c1c1c;
    --card: #f7f7f7;
    --backdrop: #8c8c8c;
    --card-edge: #d6d6d6;
  }
  * { box-sizing: border-box; margin: 0; padding: 0; }
  html, body {
    width: 1200px;
    height: 1200px;
    overflow: hidden;
  }
  body {
    background: var(--backdrop);
    font-family: "Open Sans", Arial, sans-serif;
    color: var(--ink);
    position: relative;
  }
  .card {
    position: absolute;
    left: 150px;
    width: 900px;
    height: 514px;
    background: var(--card);
    border: 1px solid var(--card-edge);
    border-radius: 16px;
  }
  .card--front { top: 60px; }
  .card--back { top: 626px; }

  /* Front */
  .front-wordmark {
    position: absolute;
    left: 200px;
    top: 90px;
    display: flex;
    align-items: center;
    gap: 18px;
  }
  .front-wordmark__mark {
    width: 34px;
    height: 34px;
    border-radius: 50%;
    background: var(--brand-blue);
    flex: none;
  }
  .front-wordmark__name {
    font-weight: 800;
    font-size: 46px;
    line-height: 1.05;
    letter-spacing: 0.5px;
    color: var(--ink);
  }
  .contact-person {
    position: absolute;
    left: 60px;
    bottom: 52px;
    line-height: 1.25;
  }
  .contact-person__name {
    font-weight: 800;
    font-size: 30px;
    letter-spacing: 3px;
    color: var(--brand-blue);
  }
  .contact-person__role,
  .contact-person__email {
    font-size: 25px;
    color: var(--ink);
  }
  .company-address {
    position: absolute;
    right: 56px;
    bottom: 150px;
    text-align: right;
    font-size: 23px;
    line-height: 1.2;
    letter-spacing: 1px;
    color: var(--ink);
  }
  .company-address__country { text-align: center; padding-left: 80px; }

  /* Back */
  .back-lockup {
    position: absolute;
    inset: 0;
    display: flex;
    flex-direction: column;
    align-items: center;
    justify-content: center;
    gap: 10px;
  }
  .back-lockup__row {
    display: flex;
    align-items: center;
    gap: 20px;
  }
  .back-lockup__mark {
    width: 40px;
    height: 40px;
    border-radius: 50%;
    background: var(--brand-blue);
  }
  .back-lockup__url {
    font-weight: 600;
    font-size: 52px;
    letter-spacing: -1px;
    color: var(--ink);
  }
  .back-lockup__slogan {
    font-size: 36px;
    color: var(--brand-blue);
    letter-spacing: -0.5px;
  }
</style>
</head>
<body>
  <section class="card card--front" aria-label="Card front">
    <div class="front-wordmark">
      <span class="front-wordmark__mark"></span>
      <span class="front-wordmark__name">TAMARIND<br>RIDGELINE MEDIA</span>
    </div>

    <address class="company-address" style="font-style:normal">
      #2714 - 582 E. Halvern<br>
      St. Vancouver, B.C. V7K2R4<br>
      <span class="company-address__country">CANADA</span><br>
      Phone: 604 317 8842
    </address>

    <div class="contact-person">
      <p class="contact-person__name">Owen Farsk</p>
      <p class="contact-person__role">Director of Sales &amp; Marketing</p>
      <p class="contact-person__email">owen@tamarindridgeline.biz</p>
    </div>
  </section>

  <section class="card card--back" aria-label="Card back">
    <div class="back-lockup">
      <div class="back-lockup__row">
        <span class="back-lockup__mark"></span>
        <span class="back-lockup__url">www.tamarindridgeline.biz</span>
      </div>
      <p class="back-lockup__slogan">Your information gateway</p>
    </div>
  </section>
</body>
</html>
```